Business cards and stationary for training company
Company in Japan specializing in corporate training
Business cards and stationary for training company  - Corporate Services
Creative Brief
Use specific fonts
Please help with this
Professional
Mason Whitfield
President
4-17-3 Harunomiya, Kita, Tokyo 114-0026
mason@brightpathlearninggroup.example
BrightpathLearningGroup.example
Will update information soon
I'm thinking to use one side for logo and other for contact info, however I need English and Japanese writing
Concepts
Business Cards and Stationery for new compliance company.
Business Cards and Stationery for Background Check Company
Leftnut Leftnut
Thank you everyone for the great designs. I will be using the stationary for rinted material and would need to think printer friendly. Thus, would it be possible to see letter head with a simple design that will look good in a thirty page booklet? Thank you.
Great so far, however it would great to see some stationary

```html
<!DOCTYPE html>
<html lang="en">
<head>
<meta charset="utf-8">
<title>Brightpath Learning Group – Business Card</title>
<link rel="stylesheet" href="https://fonts.googleapis.com/css2?family=Archivo:wght@800&family=Open+Sans:wght@400;600&display=swap">
<style>
  :root {
    --backdrop: #767676;
    --brand-blue: #1f5fa8;
    --brand-blue-dark: #184f8f;
    --card-white: #ffffff;
    --ink: #3a3a3a;
    --muted: #9a9a9a;
    --rule: #dcdcdc;
  }
  * { box-sizing: border-box; margin: 0; padding: 0; }
  html, body {
    width: 1200px;
    height: 908px;
    overflow: hidden;
    background: var(--backdrop);
  }
  .stage {
    width: 1200px;
    height: 908px;
    display: flex;
    align-items: center;
    justify-content: center;
    gap: 40px;
  }
  .card {
    width: 540px;
    height: 310px;
    border-radius: 24px;
    position: relative;
    overflow: hidden;
  }
  .card--front {
    background: linear-gradient(135deg, var(--brand-blue) 0%, var(--brand-blue-dark) 100%);
    display: flex;
    align-items: center;
    justify-content: center;
  }
  .card--back { background: var(--card-white); }

  .wordmark {
    display: flex;
    align-items: center;
    gap: 12px;
    font-family: "Archivo", "Arial", sans-serif;
    font-weight: 800;
    text-transform: uppercase;
    letter-spacing: 0.5px;
    line-height: 1;
    white-space: nowrap;
  }
  .wordmark__square { width: 30px; height: 30px; flex: none; }
  .card--front .wordmark { color: var(--card-white); font-size: 26px; }
  .card--front .wordmark__square { background: var(--card-white); }

  .card--back .wordmark {
    position: absolute;
    left: 40px;
    top: 72px;
    color: var(--brand-blue);
    font-size: 21px;
  }
  .card--back .wordmark__square { background: var(--brand-blue); width: 26px; height: 26px; }

  .holder {
    position: absolute;
    left: 40px;
    top: 192px;
    font-family: "Open Sans", "Arial", sans-serif;
  }
  .holder__name { color: var(--brand-blue); font-size: 17px; font-weight: 600; line-height: 1.3; }
  .holder__title { color: var(--muted); font-size: 12px; margin-top: 2px; }

  .divider {
    position: absolute;
    left: 282px;
    top: 112px;
    width: 1px;
    height: 150px;
    background: var(--rule);
  }

  .contact {
    position: absolute;
    left: 298px;
    top: 118px;
    list-style: none;
    font-family: "Open Sans", "Arial", sans-serif;
    font-size: 10px;
    color: var(--ink);
    line-height: 1.45;
    white-space: nowrap;
  }
  .contact__address { margin-bottom: 8px; }
  .contact__item {
    display: flex;
    align-items: center;
    gap: 6px;
    margin-bottom: 3px;
  }
  .contact__icon { width: 11px; height: 11px; flex: none; }
</style>
</head>
<body>
<main class="stage">
  <section class="card card--front" aria-label="Card front">
    <div class="wordmark">
      <span class="wordmark__square"></span>
      <span>Brightpath Learning Group</span>
    </div>
  </section>

  <section class="card card--back" aria-label="Card back">
    <div class="wordmark">
      <span class="wordmark__square"></span>
      <span>Brightpath Learning Group</span>
    </div>

    <div class="holder">
      <p class="holder__name">Mason Whitfield</p>
      <p class="holder__title">President</p>
    </div>

    <div class="divider"></div>

    <ul class="contact">
      <li class="contact__address">4-17-3 Harunomiya, Kita,<br>Tokyo 114-0026</li>
      <li class="contact__item">
        <svg class="contact__icon" viewBox="0 0 12 12" aria-hidden="true"><circle cx="6" cy="6" r="6" fill="#1f5fa8"/><path d="M4 3.2l1 1.4-.6.7c.4.8 1 1.4 1.8 1.8l.7-.6 1.4 1-.5 1.1C5.6 8.4 3.6 6.4 3.4 4z" fill="#fff"/></svg>
        <span>(03) 5550-2184</span>
      </li>
      <li class="contact__item">
        <svg class="contact__icon" viewBox="0 0 12 12" aria-hidden="true"><circle cx="6" cy="6" r="6" fill="#1f5fa8"/><rect x="3" y="4" width="6" height="4.2" fill="none" stroke="#fff" stroke-width=".9"/><path d="M3 4l3 2.3L9 4" fill="none" stroke="#fff" stroke-width=".9"/></svg>
        <span>mason@brightpathlearninggroup.example</span>
      </li>
      <li class="contact__item">
        <svg class="contact__icon" viewBox="0 0 12 12" aria-hidden="true"><circle cx="6" cy="6" r="6" fill="#1f5fa8"/><circle cx="6" cy="6" r="3" fill="none" stroke="#fff" stroke-width=".9"/><path d="M3 6h6M6 3c-1.3 1.6-1.3 4.4 0 6M6 3c1.3 1.6 1.3 4.4 0 6" fill="none" stroke="#fff" stroke-width=".7"/></svg>
        <span>BrightpathLearningGroup.example</span>
      </li>
    </ul>
  </section>
</main>
</body>
</html>
```